KBT Business Cards

We require business cards for our business. We would like a matte black back to the card, with our logo centred in the middle. The front side of the card is open to design.

Target Market(s)

Clients looking for legal services (professional)

Industry/Entity Type

Legal

Contact Information for Business Card

Doran Kelbrath
Partner
Mobile: 0461 738 524
Email: doran@kbtlaw.co
Website: www.kbtlaw.co
Level 3, 118 Wendmore Street
Sydney NSW 2000

Font styles to use
Other font styles liked:
• Avenir

Colors
f04a50
ffffff
1b1b1b

Requirements
Must have
• Black back with logo included in the centre of the card.
• Our font is Avenir.

```html
<!DOCTYPE html>
<html lang="en">
<head>
<meta charset="utf-8">
<title>KBT Legal – Business Cards</title>
<link rel="stylesheet" href="https://fonts.googleapis.com/css2?family=Nunito+Sans:wght@400;600;800&display=swap">
<style>
  :root {
    --backdrop: #2a2a2a;
    --card: #1b1b1b;
    --accent: #d42155;
    --white: #ffffff;
    --muted: #e6e6e6;
  }
  * { box-sizing: border-box; margin: 0; padding: 0; }
  html, body {
    width: 1200px; height: 900px; overflow: hidden;
    background: var(--backdrop);
    font-family: "Nunito Sans", "Avenir", sans-serif;
  }
  .sheet {
    position: relative; width: 1200px; height: 900px;
  }
  .card {
    position: absolute; left: 250px; width: 700px; height: 400px;
    background: var(--card);
    box-shadow: 0 10px 30px rgba(0,0,0,.45);
  }
  .card--back { top: 40px; }
  .card--front { top: 470px; }

  /* Back: centred wordmark */
  .card--back .wordmark {
    position: absolute; left: 50%; top: 50%;
    transform: translate(-50%, -50%);
    display: flex; align-items: center; gap: 18px;
  }
  .wordmark__square {
    width: 34px; height: 34px; background: var(--accent);
  }
  .wordmark__name {
    color: var(--white); font-weight: 800; font-size: 40px;
    letter-spacing: 1px; text-transform: uppercase; line-height: 1;
  }

  /* Front */
  .front__brand {
    position: absolute; left: 52px; top: 44px;
    color: var(--white); font-weight: 800; font-size: 42px;
    letter-spacing: 1px; text-transform: uppercase; line-height: 1;
  }
  .front__person { position: absolute; left: 52px; top: 130px; }
  .person__name {
    color: var(--accent); font-weight: 600; font-size: 26px;
    text-transform: uppercase; letter-spacing: .5px; line-height: 1.1;
  }
  .person__role { color: var(--muted); font-size: 18px; margin-top: 2px; }
  .front__address {
    position: absolute; left: 52px; top: 210px;
    color: var(--muted); font-size: 18px; line-height: 1.45;
  }
  .front__contact {
    position: absolute; left: 52px; top: 282px;
    list-style: none; color: var(--muted); font-size: 18px; line-height: 1.5;
  }
  .front__contact li { display: flex; align-items: center; gap: 10px; }
  .front__contact svg { width: 13px; height: 13px; flex: none; }

  .front__mark {
    position: absolute; right: 56px; top: 150px;
    display: flex; align-items: center; gap: 22px;
  }
  .front__mark .wordmark__square { width: 64px; height: 64px; }
  .front__mark .wordmark__name { font-size: 92px; letter-spacing: 3px; }
</style>
</head>
<body>
<main class="sheet">
  <section class="card card--back" aria-label="Card back">
    <div class="wordmark">
      <span class="wordmark__square"></span>
      <span class="wordmark__name">KBT Legal</span>
    </div>
  </section>

  <section class="card card--front" aria-label="Card front">
    <h1 class="front__brand">KBT Legal</h1>

    <div class="front__person">
      <p class="person__name">Doran Kelbrath</p>
      <p class="person__role">General Manager</p>
    </div>

    <address class="front__address" style="font-style:normal">
      Level 3, 118 Wendmore Street<br>
      Sydney NSW 2000
    </address>

    <ul class="front__contact">
      <li>
        <svg viewBox="0 0 16 16" aria-hidden="true"><path fill="var(--accent)" d="M4 1l2.5 3-1.5 2c1 2 2.5 3.5 4.5 4.5l2-1.5 3 2.5-1.5 3C7 14 2 9 1 2.5z"/></svg>
        0461 738 524
      </li>
      <li>
        <svg viewBox="0 0 16 16" aria-hidden="true"><rect x="1" y="3" width="14" height="10" fill="none" stroke="var(--accent)" stroke-width="1.6"/><path d="M1 3l7 6 7-6" fill="none" stroke="var(--accent)" stroke-width="1.6"/></svg>
        doran@kbtlaw.co
      </li>
      <li>
        <svg viewBox="0 0 16 16" aria-hidden="true"><g fill="none" stroke="var(--accent)" stroke-width="1.4"><circle cx="8" cy="8" r="6.5"/><ellipse cx="8" cy="8" rx="3" ry="6.5"/><path d="M1.5 8h13"/></g></svg>
        www.kbtlaw.co
      </li>
    </ul>

    <div class="front__mark">
      <span class="wordmark__square"></span>
      <span class="wordmark__name">KBT</span>
    </div>
  </section>
</main>
</body>
</html>
```